Letter design, envelope design, and more

Hello, we the Tavrin Gmbh are looking for our shop. Letter C5. Design does not have to be like a business card, so it can have straight lines. Only the color is important. The logo is the text under TaVRin omit.It should not be playful but Profesionel

Font styles to use
Sans Serif

Colors
0555a3
3176b5
85abd2
85cae6
34a7d8
0792cd
cee9f5
cfdfed
000000

Requirements
Must have
• Color like business card, Please, with the text under TaVRin, Correct address Lindmattstr. 4 Zip code 9517 Goldach, as well as Couvert Without addressing only design and logo with TaVrn
Nice to have
• more writing articles
Should not have
• Not too colored, Text under TaVRin, bright colors

```html
<!DOCTYPE html>
<html lang="en">
<head>
<meta charset="utf-8">
<title>Tavrin Gmbh – Stationery</title>
<link href="https://fonts.googleapis.com/css2?family=Lato:wght@400;700&family=Kaushan+Script&display=swap" rel="stylesheet">
<style>
:root{
  --navy:#1f2562;
  --steel:#7d9bb5;
  --rule:#2f6fae;
  --ink:#3a3a3a;
  --paper:#ffffff;
  --backdrop:#cdcfd2;
  --edge:#b9bcc0;
}
*{box-sizing:border-box;margin:0;padding:0}
html,body{width:1200px;height:630px;overflow:hidden;background:var(--backdrop);font-family:'Lato',sans-serif}
.stage{position:relative;width:1200px;height:630px}

.wordmark{display:flex;align-items:center;gap:6px;color:var(--navy);font-weight:700;letter-spacing:1px;white-space:nowrap}
.wordmark .dot{width:10px;height:10px;background:var(--navy)}

/* Letterhead */
.letter{position:absolute;left:31px;top:45px;width:388px;height:546px;background:linear-gradient(135deg,#fff 45%,#e9eaec);border:1px solid var(--edge)}
.letter .wordmark{position:absolute;left:23px;top:18px;font-size:24px}
.letter .head-rule{position:absolute;left:0;top:61px;width:389px;height:2px;background:var(--rule)}
.letter .web{position:absolute;right:16px;top:53px;background:var(--paper);padding:0 8px;font-size:9.5px;letter-spacing:1.6px;color:var(--ink);line-height:18px}
.letter .web b{font-weight:400;color:var(--steel)}
.letter .body{position:absolute;left:23px;top:97px;width:348px}
.salutation{font-size:10.5px;font-weight:700;color:var(--navy);margin-bottom:6px}
.body p{font-size:6.9px;line-height:11.8px;color:var(--ink);text-align:justify;margin-bottom:9px}
.closing{position:absolute;left:23px;top:427px;font-size:12px;color:var(--ink)}
.signature{position:absolute;left:23px;top:444px;font-family:'Kaushan Script',cursive;font-size:19px;color:var(--navy)}
.contact{position:absolute;left:0;right:0;top:526px;display:flex;justify-content:center;gap:8px;font-size:7.5px;color:var(--ink)}
.contact span{display:flex;align-items:center;gap:3px}
.contact .sep{width:1px;height:9px;background:#c4c4c4}
.contact svg{width:7px;height:7px}

/* Envelopes */
.envelope{position:absolute;background:var(--paper);border:1px solid var(--edge)}
.env-back{left:600px;top:66px;width:578px;height:258px}
.env-mid{left:558px;top:176px;width:578px;height:260px}
.env-front{left:462px;top:292px;width:577px;height:258px}
.flap{position:absolute;left:0;top:0}
.flap-mark{position:absolute;left:0;right:0;text-align:center;font-weight:700;letter-spacing:3px}
.env-back .flap-mark{top:38px;color:var(--paper);font-size:26px}
.env-mid .flap-mark{top:36px;color:var(--navy);font-size:26px}
.env-front .wordmark{position:absolute;left:16px;top:16px;font-size:26px}
.env-front .address{position:absolute;left:16px;top:66px;display:flex;align-items:center;gap:5px;font-size:10.5px;color:var(--ink)}
.env-front .address svg{width:10px;height:10px}
.env-front .foot-rule{position:absolute;left:0;right:0;top:240px;height:1.5px;background:var(--navy)}
.env-front .web{position:absolute;left:50%;top:232px;transform:translateX(-50%);background:var(--paper);padding:0 10px;font-size:10px;letter-spacing:1.8px;color:var(--ink);line-height:17px}
.env-front .web b{font-weight:400;color:var(--steel)}
</style>
</head>
<body>
<div class="stage">

  <section class="letter">
    <div class="wordmark"><span class="dot"></span>TAVRIN GMBH</div>
    <div class="head-rule"></div>
    <div class="web">www.<b>tavrin</b>.ch</div>
    <div class="body">
      <div class="salutation">Dear Mr. Lorem,</div>
      <p>Lorem ipsum dolor sit amet, consectetuer adipiscing elit, sed diam nonummy nibh euismod tincidunt ut laoreet dolore magna aliquam erat volutpat. Ut wisi enim ad minim veniam, quis nostrud exerci tation ullamcorper suscipit lobortis nisl ut aliquip ex ea commodo consequat. Duis autem vel eum iriure dolor in hendiusto odio dignissim qui blandit praesent luptatum zzril delenit facilisi.</p>
      <p>Lorem ipsum dolor sit amet, consectetuer adipiscing elit, sed diam nonummy nibh euismod tincidunt ut laoreet dolore magna aliquam erat volutpat. Ut wisi enim ad minim veniam, quis nostrud exerci tation ullamcorper suscipit lobortis nisl ut aliquip ex ea commodo consequat.</p>
      <p>Lorem ipsum dolor sit amet, consectetuer adipiscing elit, sed diam nonummy nibh euismod tincidunt ut laoreet dolore magna aliquam erat volutpat. Ut wisi enim ad minim veniam, quis nostrud exerci tation ullamcorper suscipit lobortis nisl ut aliquip ex ea commodo consequat. Duis autem vel eum iriure dolor in hendiusto odio dignissim qui blandit praesent luptatum zzril delenit facilisi.</p>
      <p>Lorem ipsum dolor sit amet, consectetuer adipiscing elit, sed diam nonummy nibh euismod tincidunt ut laoreet dolore magna aliquam erat volutpat. Ut wisi enim ad minim veniam, quis nostrud exerci tation ullamcorper suscipit lobortis nisl ut aliquip ex ea commodo consequat.</p>
      <p>Lorem ipsum dolor sit amet, consectetuer adipiscing elit, sed diam nonummy nibh euismod tincidunt ut laoreet dolore magna aliquam erat volutpat. Ut wisi enim ad minim veniam, quis nostrud exerci tation ullamcorper suscipit lobortis nisl ut aliquip ex ea commodo consequat. Duis autem vel eum iriure dolor in hendiusto odio dignissim qui blandit praesent luptatum zzril delenit facilisi.</p>
      <p>Lorem ipsum dolor sit amet, consectetuer adipiscing elit, sed diam nonummy nibh euismod tincidunt ut laoreet dolore magna aliquam erat volutpat. Ut wisi enim ad minim veniam, quis nostrud exerci tation ullamcorper suscipit lobortis nisl ut aliquip ex ea commodo consequat.</p>
    </div>
    <div class="closing">Sincerely Your,</div>
    <div class="signature">Your Name</div>
    <div class="contact">
      <span><svg viewBox="0 0 10 10"><path d="M5 .5a3.3 3.3 0 0 0-3.3 3.3C1.7 6.3 5 9.5 5 9.5s3.3-3.2 3.3-5.7A3.3 3.3 0 0 0 5 .5z" fill="none" stroke="#1f2562" stroke-width="1.2"/><circle cx="5" cy="3.8" r="1.1" fill="#1f2562"/></svg>Lindmattstr. 4, 9517 Goldach</span>
      <span class="sep"></span>
      <span><svg viewBox="0 0 10 10"><path d="M2.5 1l1.6 2-1 1.2a5.5 5.5 0 0 0 2.7 2.7l1.2-1 2 1.6-1.2 1.6C4.6 9 1 5.4.9 2.2z" fill="#1f2562"/></svg>+41 71 555 20 40</span>
      <span class="sep"></span>
      <span><svg viewBox="0 0 10 10"><rect x=".5" y="2" width="9" height="6" fill="#1f2562"/><path d="M.5 2L5 5.5 9.5 2" fill="none" stroke="#fff" stroke-width=".8"/></svg>info@tavrin.ch</span>
    </div>
  </section>

  <section class="envelope env-back">
    <svg class="flap" width="578" height="110" viewBox="0 0 578 110"><path d="M0 0H578L566 22Q560 40 530 48L330 98Q289 110 248 98L48 48Q18 40 12 22Z" fill="var(--steel)"/></svg>
    <div class="flap-mark">TAVRIN</div>
  </section>

  <section class="envelope env-mid">
    <svg class="flap" width="578" height="110" viewBox="0 0 578 110"><path d="M0 0L10 24Q16 46 48 56L248 98Q289 110 330 98L530 56Q562 46 568 24L578 0" fill="none" stroke="#b5b7ba" stroke-width="1"/></svg>
    <div class="flap-mark">TAVRIN</div>
  </section>

  <section class="envelope env-front">
    <div class="wordmark"><span class="dot"></span>TAVRIN GMBH</div>
    <div class="address"><svg viewBox="0 0 10 10"><path d="M5 .5a3.3 3.3 0 0 0-3.3 3.3C1.7 6.3 5 9.5 5 9.5s3.3-3.2 3.3-5.7A3.3 3.3 0 0 0 5 .5z" fill="none" stroke="#1f2562" stroke-width="1.1"/><circle cx="5" cy="3.8" r="1.1" fill="#1f2562"/></svg>Lindmattstr. 4, 9517 Goldach</div>
    <div class="foot-rule"></div>
    <div class="web">www.<b>tavrin</b>.ch</div>
  </section>

</div>
</body>
</html>
```